Stated Income Loans

Flyer design to be used on social media platforms (i.e. Facebook, Instagram etc.)

Target Market(s)

Real Estate Investors

Requirements
Must have
• INVESTOR STATED INCOME LOANS
• "IT'S TIME TO THINK BIG"
• * Purchase or Refinance up to 3 Million
• * No Income Docs or Bank Statements
• * Vacant Properties Allowed
• * Minimum Credit Score 620
• * Cash Out up to 80%
• Same Day Pre-Approval
• 20-30 Day Close
• Call Marcus Delvane today...
• Brightkeel Lending Group, Inc.
• Phone (800) 416-9027 x 42
• Direct (240) 958-2046
• www.brightkeelhub.com
• NMLS #386710 / #57483
Should not have
• Do not use same color scheme as website. Be creative.

```html
<!DOCTYPE html>
<html lang="en">
<head>
<meta charset="utf-8">
<title>Investor Stated Income Loans</title>
<link rel="stylesheet" href="https://fonts.googleapis.com/css2?family=Jost:ital,wght@0,300;0,400;0,500;0,600;0,700;1,300&display=swap">
<style>
  :root {
    --teal: #0f4c68;
    --teal-dark: #0a3a51;
    --paper: #f4f3f1;
    --ink: #1d2a33;
    --white: #ffffff;
    --photo-light: #d9d9d9;
    --photo-dark: #1e1e1e;
  }
  * { margin: 0; padding: 0; box-sizing: border-box; }
  html, body { width: 957px; height: 1200px; overflow: hidden; }
  body { background: var(--paper); font-family: "Jost", sans-serif; color: var(--ink); }
  .flyer { position: relative; width: 957px; height: 1200px; overflow: hidden; background: var(--paper); }

  .title-band {
    position: absolute; left: 0; top: 0; width: 100%; height: 100px;
    background: var(--teal); display: flex; align-items: center; justify-content: center;
  }
  .title-band h1 {
    color: var(--white); font-weight: 600; font-size: 46px; letter-spacing: 0.5px; text-transform: uppercase;
  }

  .hero-photo {
    position: absolute; left: 0; top: 100px; width: 100%; height: 460px;
    background: linear-gradient(160deg, #3a3a3a 0%, #8a8a8a 30%, var(--photo-light) 48%, #6b6b6b 70%, var(--photo-dark) 100%);
    clip-path: polygon(0 0, 100% 0, 100% 100%, 0 92%);
  }

  .headline-box {
    position: absolute; left: 0; top: 250px; width: 450px; height: 210px;
    background: rgba(15, 76, 104, 0.88); color: var(--white); padding: 14px 0 0 18px;
  }
  .headline-box .line-a { font-weight: 300; font-style: italic; font-size: 52px; line-height: 0.95; }
  .headline-box .line-b { font-weight: 300; font-size: 62px; line-height: 1; }
  .headline-box .line-c { font-weight: 700; font-size: 68px; line-height: 1; letter-spacing: 1px; }

  .money-photo {
    position: absolute; left: 0; top: 0; width: 957px; height: 1200px;
    background: linear-gradient(135deg, #bdbdbd 0%, #5a5a5a 40%, var(--photo-dark) 100%);
    clip-path: polygon(640px 560px, 957px 560px, 957px 895px, 460px 895px);
  }
  .money-stripe {
    position: absolute; left: 0; top: 0; width: 957px; height: 1200px;
    background: var(--teal);
    clip-path: polygon(628px 560px, 642px 560px, 462px 895px, 448px 895px);
  }

  .features { position: absolute; left: 80px; top: 572px; list-style: none; }
  .features li {
    display: flex; align-items: center; gap: 18px; height: 40px;
    font-size: 24px; font-weight: 400; color: var(--ink);
  }
  .features .tick { width: 26px; height: 26px; flex: none; }
  .features em { font-style: normal; color: var(--teal); font-weight: 500; font-size: 31px; }
  .features .accent { color: var(--teal); font-weight: 500; }

  .contact-band {
    position: absolute; left: 0; top: 935px; width: 100%; height: 110px; background: var(--teal);
  }
  .brand-card {
    position: absolute; left: 40px; top: 885px; width: 360px; height: 195px;
    background: var(--white); box-shadow: 0 4px 10px rgba(0,0,0,0.18);
    display: flex; align-items: center; justify-content: center; gap: 14px; padding: 0 22px;
  }
  .brand-card .mark { width: 40px; height: 40px; border-radius: 50%; background: var(--teal); flex: none; }
  .brand-card .brand-name { font-size: 22px; font-weight: 500; color: var(--teal); line-height: 1.2; }

  .call-line {
    position: absolute; left: 430px; top: 897px; font-size: 22px; color: var(--ink);
  }
  .call-line strong { color: var(--teal); font-weight: 600; }
  .contact-details {
    position: absolute; left: 430px; top: 945px; color: var(--white); font-size: 19px; line-height: 23px;
  }

  .agent-photo {
    position: absolute; left: 720px; top: 880px; width: 210px; height: 165px;
    background: linear-gradient(180deg, #6d6d6d 0%, #2a2a2a 55%, #111 100%);
    border-radius: 90px 90px 0 0;
  }

  .social { position: absolute; left: 0; top: 1095px; width: 100%; display: flex; justify-content: center; gap: 12px; }
  .social span { width: 28px; height: 28px; border: 2px solid var(--teal); border-radius: 50%; }

  .footer-rule { position: absolute; left: 0; bottom: 0; width: 100%; height: 14px; background: var(--teal); }
</style>
</head>
<body>
<div class="flyer">
  <header class="title-band"><h1>Investor Stated Income Loans</h1></header>

  <div class="hero-photo" role="img" aria-label="Black and white photo looking up at city skyscrapers against the sky"></div>

  <div class="headline-box">
    <div class="line-a">It’s</div>
    <div class="line-b">TIME To</div>
    <div class="line-c">THINK BIG</div>
  </div>

  <div class="money-stripe"></div>
  <div class="money-photo" role="img" aria-label="Black and white photo of a roll of dollar bills over financial figures"></div>

  <ul class="features">
    <li><svg class="tick" viewBox="0 0 26 26"><circle cx="13" cy="13" r="11" fill="none" stroke="#0f4c68" stroke-width="2"/><path d="M8 13l4 4 10-11" fill="none" stroke="#0f4c68" stroke-width="2.4"/></svg><span>Purchase or Refinance up to <em>3 Million</em></span></li>
    <li><svg class="tick" viewBox="0 0 26 26"><circle cx="13" cy="13" r="11" fill="none" stroke="#0f4c68" stroke-width="2"/><path d="M8 13l4 4 10-11" fill="none" stroke="#0f4c68" stroke-width="2.4"/></svg><span><span class="accent">No</span> Income Docs or Bank Statements</span></li>
    <li><svg class="tick" viewBox="0 0 26 26"><circle cx="13" cy="13" r="11" fill="none" stroke="#0f4c68" stroke-width="2"/><path d="M8 13l4 4 10-11" fill="none" stroke="#0f4c68" stroke-width="2.4"/></svg><span>Vacant Properties Allowed</span></li>
    <li><svg class="tick" viewBox="0 0 26 26"><circle cx="13" cy="13" r="11" fill="none" stroke="#0f4c68" stroke-width="2"/><path d="M8 13l4 4 10-11" fill="none" stroke="#0f4c68" stroke-width="2.4"/></svg><span>Minimum Credit Score <em>620</em></span></li>
    <li><svg class="tick" viewBox="0 0 26 26"><circle cx="13" cy="13" r="11" fill="none" stroke="#0f4c68" stroke-width="2"/><path d="M8 13l4 4 10-11" fill="none" stroke="#0f4c68" stroke-width="2.4"/></svg><span>Cash Out up to <em>80%</em></span></li>
    <li><svg class="tick" viewBox="0 0 26 26"><circle cx="13" cy="13" r="11" fill="none" stroke="#0f4c68" stroke-width="2"/><path d="M8 13l4 4 10-11" fill="none" stroke="#0f4c68" stroke-width="2.4"/></svg><span>Same Day <span class="accent">Pre-Approval</span></span></li>
    <li><svg class="tick" viewBox="0 0 26 26"><circle cx="13" cy="13" r="11" fill="none" stroke="#0f4c68" stroke-width="2"/><path d="M8 13l4 4 10-11" fill="none" stroke="#0f4c68" stroke-width="2.4"/></svg><span><em>20-30</em> Day Close</span></li>
  </ul>

  <div class="contact-band"></div>

  <div class="brand-card">
    <span class="mark"></span>
    <span class="brand-name">Brightkeel Lending Group, Inc.</span>
  </div>

  <p class="call-line">Call <strong>Marcus Delvane</strong> today...</p>
  <div class="contact-details">
    <p>Phone: (800) 416-9027 x 42</p>
    <p>Direct: (240) 958-2046</p>
    <p>www.brightkeelhub.com</p>
    <p>NMLS #386710 / #57483</p>
  </div>

  <div class="agent-photo" role="img" aria-label="Portrait of the loan officer in a dark suit and tie"></div>

  <div class="social" aria-hidden="true"><span></span><span></span><span></span></div>

  <div class="footer-rule"></div>
</div>
</body>
</html>
```